Business Card Design Project

Basic business card with minimal details. I just need company name, email & web address, telephone and my name.
I would like the back of the card to be grey with my logo & company name centred.

Target Market(s)

Architects
Builders
Property Developers

Industry/Entity Type

Business

Font styles to use
Sans Serif

Colors

Designer to choose colors to be used in the design.

Requirements
Must have
• Tallow Crest
Rupert Hazelby - Director
M: 0427 915203
E: rupert@tallowcrest.com.au
W: www.tallowcrest.com.au
Should not have
• No other images or pictures

```html
<!DOCTYPE html>
<html lang="en">
<head>
<meta charset="utf-8">
<title>Tallow Crest – Business Cards</title>
<link rel="stylesheet" href="https://fonts.googleapis.com/css2?family=Open+Sans:wght@400;600&family=PT+Serif:wght@400&display=swap">
<style>
  :root {
    --backdrop: #b9bcbf;
    --slate-light: #6b7d88;
    --slate-dark: #4a5c6b;
    --paper: #ffffff;
    --crimson: #a6173a;
    --ink-light: #ffffff;
    --ink-dark: #4a5c6b;
    --shadow: 0 6px 14px rgba(0,0,0,0.35);
  }
  * { margin: 0; padding: 0; box-sizing: border-box; }
  html, body { width: 1200px; height: 1000px; overflow: hidden; }
  body {
    background: var(--backdrop);
    font-family: "Open Sans", Arial, sans-serif;
    position: relative;
  }
  .card {
    position: absolute;
    box-shadow: var(--shadow);
    overflow: hidden;
  }

  /* Front card */
  .card--front {
    left: 300px; top: 70px; width: 560px; height: 260px;
    background: var(--slate-light);
    color: var(--ink-light);
  }
  .front__brand {
    position: absolute; left: 36px; top: 110px;
    display: flex; align-items: center; gap: 12px;
  }
  .front__brand-square {
    width: 22px; height: 22px; background: var(--ink-light);
  }
  .front__brand-name {
    font-size: 26px; font-weight: 600; letter-spacing: 1px;
    color: var(--ink-light);
  }
  .front__person {
    position: absolute; left: 306px; top: 36px;
  }
  .front__name {
    font-family: "PT Serif", Georgia, serif;
    font-size: 19px; letter-spacing: 0.3px;
  }
  .front__title { font-size: 11px; margin-top: 1px; }
  .front__contacts {
    position: absolute; left: 306px; top: 168px;
    list-style: none; font-size: 13px; line-height: 21px;
  }
  .front__label {
    display: inline-block; width: 22px;
    color: var(--crimson); font-weight: 600;
  }

  /* Back cards */
  .card--back {
    width: 490px; height: 250px;
    display: flex; flex-direction: column; align-items: center; justify-content: center;
    gap: 26px;
  }
  .card--back-left { left: 45px; top: 420px; background: var(--slate-dark); }
  .card--back-right { left: 660px; top: 430px; background: var(--paper); }
  .card--back-bottom { left: 385px; top: 715px; background: var(--slate-dark); }
  .back__square { width: 46px; height: 46px; }
  .back__name {
    font-size: 34px; font-weight: 600; letter-spacing: 3px; text-transform: uppercase;
  }
  .card--back-left .back__square,
  .card--back-right .back__square { background: var(--crimson); }
  .card--back-bottom .back__square { background: var(--ink-light); }
  .card--back-left .back__name,
  .card--back-bottom .back__name { color: var(--ink-light); }
  .card--back-right .back__name { color: var(--ink-dark); }
</style>
</head>
<body>
  <section class="card card--front" aria-label="Business card front">
    <div class="front__brand">
      <span class="front__brand-square"></span>
      <span class="front__brand-name">Tallow Crest</span>
    </div>
    <div class="front__person">
      <p class="front__name">Rupert Hazelby</p>
      <p class="front__title">Director</p>
    </div>
    <ul class="front__contacts">
      <li><span class="front__label">M</span>0427 915203</li>
      <li><span class="front__label">E</span>rupert@tallowcrest.com.au</li>
      <li><span class="front__label">W</span>www.tallowcrest.com.au</li>
    </ul>
  </section>

  <section class="card card--back card--back-left" aria-label="Business card back, dark">
    <span class="back__square"></span>
    <p class="back__name">Tallow Crest</p>
  </section>

  <section class="card card--back card--back-right" aria-label="Business card back, white">
    <span class="back__square"></span>
    <p class="back__name">Tallow Crest</p>
  </section>

  <section class="card card--back card--back-bottom" aria-label="Business card back, dark with white">
    <span class="back__square"></span>
    <p class="back__name">Tallow Crest</p>
  </section>
</body>
</html>
```